Simple and Clean business card design

We would like the design to be simple clean and to incorporate our colors.

We are open to your design and talent, we have the dots in our logo as we think of it as data points and we connect data points for people.

We are open to see the great creative and clean design you bring to the table

Contact Information for Business Card

please include: name, position, email, phone and website

Font styles to use
Sans Serif

Requirements
Must have
• my colors incorporated, simplicity
Nice to have
• lots of white space, simplicity
Should not have
• complexicity/ complex art

```html
<!DOCTYPE html>
<html lang="en">
<head>
<meta charset="utf-8">
<title>Brindle — Business Card</title>
<link href="https://fonts.googleapis.com/css2?family=Montserrat:wght@600&family=Work+Sans:wght@400;500;600&display=swap" rel="stylesheet">
<style>
  :root {
    --backdrop-top: #2e2e2e;
    --backdrop-bottom: #0d0d0d;
    --card: #1d1d1d;
    --card-edge: #262626;
    --ink: #ffffff;
    --ink-soft: #e6e6e6;
    --mark-grey: #c9c9c9;
    --brand-blue: #5b7fcf;
    --brand-yellow: #f4bd1d;
  }
  * { margin: 0; padding: 0; box-sizing: border-box; }
  html, body { width: 1200px; height: 900px; overflow: hidden; }
  body {
    background: radial-gradient(ellipse at 50% 30%, var(--backdrop-top), var(--backdrop-bottom) 75%);
    font-family: "Work Sans", Arial, sans-serif;
    display: flex;
    flex-direction: column;
    align-items: center;
    justify-content: center;
    gap: 40px;
  }
  .card {
    width: 640px;
    height: 366px;
    background: linear-gradient(135deg, var(--card-edge), var(--card) 60%);
    border-radius: 4px;
    box-shadow: 0 18px 40px rgba(0,0,0,0.55);
    position: relative;
  }
  /* Front */
  .card--front {
    display: flex;
    align-items: center;
    justify-content: center;
  }
  .wordmark {
    display: flex;
    align-items: center;
    gap: 14px;
    font-family: "Work Sans", Arial, sans-serif;
    font-weight: 600;
    letter-spacing: -1px;
  }
  .wordmark__dot {
    border-radius: 50%;
    background: var(--brand-blue);
  }
  .card--front .wordmark { font-size: 96px; color: var(--mark-grey); }
  .card--front .wordmark__dot { width: 22px; height: 22px; }

  /* Back */
  .card--back .wordmark {
    position: absolute;
    left: 48px;
    top: 38px;
    font-size: 62px;
    color: var(--ink);
    gap: 10px;
  }
  .card--back .wordmark__dot { width: 15px; height: 15px; }
  .contact {
    position: absolute;
    left: 48px;
    top: 148px;
    padding-left: 30px;
  }
  .contact__accent {
    position: absolute;
    left: 0;
    top: 6px;
    width: 9px;
    height: 44px;
    background: var(--brand-yellow);
  }
  .contact__name {
    font-family: "Montserrat", Arial, sans-serif;
    font-weight: 600;
    font-size: 26px;
    letter-spacing: 2.5px;
    color: var(--brand-blue);
    text-transform: uppercase;
    line-height: 1.1;
  }
  .contact__role {
    font-size: 19px;
    color: var(--ink-soft);
    margin-bottom: 14px;
    letter-spacing: 0.5px;
  }
  .contact__address {
    font-size: 18px;
    color: var(--ink-soft);
    line-height: 1.35;
    letter-spacing: 0.8px;
    margin-bottom: 6px;
  }
  .contact__line {
    display: flex;
    align-items: center;
    gap: 8px;
    font-size: 18px;
    color: var(--ink-soft);
    letter-spacing: 0.8px;
    line-height: 1.4;
  }
  .contact__icon {
    width: 14px;
    height: 14px;
    flex: none;
    fill: none;
    stroke: var(--brand-blue);
    stroke-width: 1.6;
  }
</style>
</head>
<body>
  <section class="card card--front" aria-label="Card front">
    <div class="wordmark"><span>Brindle</span><span class="wordmark__dot"></span></div>
  </section>

  <section class="card card--back" aria-label="Card back">
    <div class="wordmark"><span>Brindle</span><span class="wordmark__dot"></span></div>
    <div class="contact">
      <span class="contact__accent"></span>
      <h1 class="contact__name">Dorian Vale</h1>
      <p class="contact__role">Founder</p>
      <p class="contact__address">418 Cedar Hollow Lane<br>Marlow, TX 78410</p>
      <p class="contact__line">
        <svg class="contact__icon" viewBox="0 0 16 16"><path d="M4 1.5l2.5 3-1.5 2a8 8 0 0 0 4.5 4.5l2-1.5 3 2.5-1.5 2.5C7 14 2 9 1.5 3z"/></svg>
        0412 558 903
      </p>
      <p class="contact__line">
        <svg class="contact__icon" viewBox="0 0 16 16"><rect x="1.5" y="3.5" width="13" height="9" rx="1"/><path d="M1.5 4l6.5 5 6.5-5"/></svg>
        hello@brindledata.com
      </p>
      <p class="contact__line">
        <svg class="contact__icon" viewBox="0 0 16 16"><circle cx="8" cy="8" r="6.5"/><ellipse cx="8" cy="8" rx="2.8" ry="6.5"/><path d="M1.5 8h13M2.5 4.8h11M2.5 11.2h11"/></svg>
        www.brindledata.com
      </p>
    </div>
  </section>
</body>
</html>
```